Stylish Business Cards Wanted

- DOUBLE SIDED Design Required -

High end, edgy cards for a corporate and personal stylist. Must include logo,
Name: Belinda Harwick
Title: Director and Stylist
telephone : +61 8 7142 5809
email: belinda@theloombriefing.example
website: theloombriefing.example
Tag: Corporate Workwear & Uniform Specialist | Personal Stylist
Would like nice icons for telephone, email, website

Target Market(s)

Businesses wanting stylish uniforms, people wanting stylish wardrobes

Industry/Entity Type

Corporate Workwear Stylist

Contact Information for Business Card

I would like black, white and gold foiling incorporated in the design - possibly a touch of the other colours on my branding guide attached Name: Belinda Harwick Title: Director and Stylist telephone : +61 8 7142 5809 email: belinda@theloombriefing.example website: theloombriefing.example Tag: Corporate Workwear & Uniform Specialist | Personal Stylist Would like nice icons for telephone, email, website

Font styles to use
Other font styles liked:
• Raleway

Colors

Designer to choose colors to be used in the design.

Requirements
Must have
• Gold foil accents

```html
<!DOCTYPE html>
<html lang="en">
<head>
<meta charset="utf-8">
<title>The Loom Briefing — Business Cards</title>
<link rel="stylesheet" href="https://fonts.googleapis.com/css2?family=Raleway:wght@500;600&family=Roboto:wght@400&family=Dancing+Script:wght@500&display=swap">
<style>
  :root {
    --backdrop: #2b2b2d;
    --card: #fbfbfa;
    --gold: #c9a235;
    --navy: #1c2235;
    --ink: #222426;
  }
  * { box-sizing: border-box; margin: 0; padding: 0; }
  html, body { width: 799px; height: 1200px; overflow: hidden; }
  body {
    background: var(--backdrop);
    display: flex;
    flex-direction: column;
    align-items: center;
    justify-content: center;
    gap: 110px;
    font-family: "Roboto", Arial, sans-serif;
  }
  .card {
    position: relative;
    width: 630px;
    height: 360px;
    background: var(--card);
    border-radius: 26px;
    box-shadow: 0 14px 34px rgba(0,0,0,0.45);
  }
  .card--front {
    display: flex;
    align-items: center;
    justify-content: center;
  }
  .brand-name {
    font-family: "Raleway", Arial, sans-serif;
    font-weight: 600;
    letter-spacing: 0.04em;
    text-transform: uppercase;
  }
  .card--front .brand-name {
    color: var(--gold);
    font-size: 46px;
    text-align: center;
    line-height: 1.15;
  }
  .holder {
    position: absolute;
    left: 44px;
    top: 40px;
  }
  .holder__name {
    font-family: "Dancing Script", cursive;
    font-weight: 500;
    font-size: 36px;
    color: var(--gold);
    line-height: 1;
  }
  .holder__title {
    font-size: 15px;
    color: var(--ink);
    margin-top: 4px;
  }
  .contact {
    position: absolute;
    left: 44px;
    top: 168px;
    list-style: none;
  }
  .contact__item {
    display: flex;
    align-items: center;
    gap: 10px;
    font-size: 16px;
    color: var(--ink);
    margin-bottom: 7px;
  }
  .contact__icon { width: 15px; height: 15px; flex: none; }
  .card--back .brand-name {
    position: absolute;
    right: 40px;
    top: 150px;
    color: var(--navy);
    font-size: 24px;
    text-align: center;
    line-height: 1.2;
  }
  .tagline {
    position: absolute;
    left: 44px;
    bottom: 40px;
    font-family: "Dancing Script", cursive;
    font-size: 22px;
    color: var(--navy);
  }
  .tagline__divider { color: var(--gold); margin: 0 8px; }
</style>
</head>
<body>
  <section class="card card--front" aria-label="Card front">
    <p class="brand-name">The Loom<br>Briefing</p>
  </section>

  <section class="card card--back" aria-label="Card back">
    <div class="holder">
      <p class="holder__name">Belinda Harwick</p>
      <p class="holder__title">Director and Stylist</p>
    </div>

    <ul class="contact">
      <li class="contact__item">
        <svg class="contact__icon" viewBox="0 0 16 16" aria-hidden="true">
          <circle cx="8" cy="8" r="7" fill="none" stroke="var(--gold)" stroke-width="1.4"/>
          <path d="M5.6 4.6l1.3 1.4-.7 1a5 5 0 0 0 2.8 2.8l1-.7 1.4 1.3-.8 1c-3.2-.3-5.7-2.8-6-6z" fill="var(--gold)"/>
        </svg>
        +61 8 7142 5809
      </li>
      <li class="contact__item">
        <svg class="contact__icon" viewBox="0 0 16 16" aria-hidden="true">
          <rect x="1.5" y="3.5" width="13" height="9" rx="1" fill="none" stroke="var(--gold)" stroke-width="1.4"/>
          <path d="M2 4l6 5 6-5" fill="none" stroke="var(--gold)" stroke-width="1.4"/>
        </svg>
        belinda@theloombriefing.example
      </li>
      <li class="contact__item">
        <svg class="contact__icon" viewBox="0 0 16 16" aria-hidden="true">
          <circle cx="8" cy="8" r="6.5" fill="none" stroke="var(--gold)" stroke-width="1.3"/>
          <ellipse cx="8" cy="8" rx="2.8" ry="6.5" fill="none" stroke="var(--gold)" stroke-width="1.1"/>
          <path d="M1.5 8h13M2.5 5h11M2.5 11h11" stroke="var(--gold)" stroke-width="1"/>
        </svg>
        www.theloombriefing.example
      </li>
    </ul>

    <p class="brand-name">The Loom<br>Briefing</p>

    <p class="tagline">Corporate Workwear &amp; Uniform Specialist<span class="tagline__divider">|</span>Personal Stylist</p>
  </section>
</body>
</html>
```